Business Management Fortress

Assist with enhancing a powerpoint slide by providing a few design options for consideration. I have a template but open to any creative ideas.

Internal employees and stakeholders

Business Management, Finance, Accounting

• Maintain a fortress, temple, or pyramid schema
• Scenic Background

```html
<!DOCTYPE html>
<html lang="en">
<head>
<meta charset="utf-8">
<title>Business Management Fortress</title>
<link rel="stylesheet" href="https://fonts.googleapis.com/css2?family=Open+Sans:wght@400;600;700&display=swap">
<style>
  :root {
    --scene-light: #9aabc8;
    --scene-mid: #7b8fb3;
    --scene-dark: #4e648c;
    --halo-top: #4c7ad0;
    --halo-bottom: #a9bfe4;
    --step-top: #d4d4d4;
    --step-face: #7f7f7f;
    --step-side: #6e6b58;
    --roof-light: #d6d6d6;
    --roof-panel: #a6a6a6;
    --roof-frame: #c2c2c2;
    --beam: #5f5f5f;
    --beam-end: #7a7560;
    --green-light: #548235;
    --green-dark: #375623;
    --green-top: #6aa040;
    --blue-light: #4472c4;
    --blue-dark: #2e4f86;
    --blue-top: #5b8ad8;
    --gold-light: #ffc000;
    --gold-dark: #bf9000;
    --gold-top: #ffd24d;
    --rust-light: #c55a11;
    --rust-dark: #843c0c;
    --rust-top: #e07020;
    --label: #ffffff;
    --roof-label: #ffffff;
  }
  * { margin: 0; padding: 0; box-sizing: border-box; }
  html, body { width: 1200px; height: 675px; overflow: hidden; }
  body { font-family: "Open Sans", sans-serif; }
  .slide { position: relative; width: 1200px; height: 675px; overflow: hidden; }
  .scenic-backdrop {
    position: absolute; inset: 0;
    background:
      radial-gradient(ellipse at 75% 35%, rgba(255,255,255,0.25), transparent 55%),
      linear-gradient(90deg, var(--scene-dark) 0%, var(--scene-mid) 30%, var(--scene-light) 60%, var(--scene-mid) 100%);
  }
  .fortress { position: absolute; inset: 0; width: 1200px; height: 675px; }
  .pillar-label { fill: var(--label); font-size: 27px; font-weight: 400; }
  .roof-label { fill: var(--roof-label); font-size: 24px; font-weight: 400; }
  .step-label { fill: #ffffff; font-weight: 700; }
  .fiduciary { font-size: 19px; }
  .foundation { font-size: 15.5px; }
  .icon { fill: none; stroke: #ffffff; stroke-width: 2; }
  .icon-fill { fill: #ffffff; }
</style>
</head>
<body>
<main class="slide">
  <div class="scenic-backdrop" role="img" aria-label="Softly blurred modern office interior in blue tones"></div>

  <svg class="fortress" viewBox="0 0 1280 720" aria-label="Business management temple diagram">
    <defs>
      <linearGradient id="halo" x1="0" y1="0" x2="0" y2="1">
        <stop offset="0" stop-color="var(--halo-top)"/>
        <stop offset="1" stop-color="var(--halo-bottom)"/>
      </linearGradient>
    </defs>

    <ellipse class="halo" cx="640" cy="555" rx="525" ry="145" fill="url(#halo)"/>

    <!-- foundation step -->
    <g class="step step-foundation">
      <polygon points="130,560 300,655 1160,525 1000,460" fill="var(--step-top)"/>
      <polygon points="130,560 300,655 300,700 130,600" fill="var(--step-side)"/>
      <polygon points="300,655 1160,525 1160,575 300,700" fill="var(--step-face)"/>
      <text class="step-label foundation" transform="translate(335,684) rotate(-8.6)">Accurate Financials / Internal Controls / Brand Protection / Compliance / Ethics / Cost Management</text>
    </g>

    <!-- fiduciary step -->
    <g class="step step-fiduciary">
      <polygon points="160,510 315,598 1055,485 900,420" fill="var(--step-top)"/>
      <polygon points="160,510 315,598 315,640 160,550" fill="var(--step-side)"/>
      <polygon points="315,598 1055,485 1055,525 315,640" fill="var(--step-face)"/>
      <text class="step-label fiduciary" transform="translate(568,590) rotate(-8.6)">Fiduciary Responsibilities</text>
    </g>

    <!-- top step -->
    <g class="step step-top">
      <polygon points="210,470 365,560 1010,465 860,400" fill="var(--step-top)"/>
      <polygon points="210,470 365,560 365,590 210,500" fill="var(--step-side)"/>
      <polygon points="365,560 1010,465 1010,482 365,590" fill="var(--step-face)"/>
    </g>

    <!-- pillar: strategic alliances -->
    <g class="pillar pillar-alliances">
      <polygon points="800,440 970,445 970,465 880,485 800,460" fill="var(--rust-dark)"/>
      <polygon points="880,465 970,445 970,465 880,485" fill="var(--rust-light)"/>
      <polygon points="800,290 880,290 880,460 800,445" fill="var(--rust-dark)"/>
      <polygon points="880,290 945,285 945,455 880,460" fill="var(--rust-light)"/>
      <polygon points="855,265 965,258 965,280 855,288" fill="var(--rust-top)"/>
      <rect class="icon" x="902" y="274" width="20" height="18" transform="rotate(-4 912 283)"/>
      <path class="icon" d="M906 280 l4 4 M910 280 l-4 4 M914 288 l5 -6"/>
      <text class="pillar-label" transform="translate(904,450) rotate(-90)">Strategic</text>
      <text class="pillar-label" transform="translate(934,450) rotate(-90)">Alliances</text>
    </g>

    <!-- pillar: intelligence -->
    <g class="pillar pillar-intelligence">
      <polygon points="645,450 820,470 820,490 710,505 645,480" fill="var(--gold-dark)"/>
      <polygon points="710,485 820,470 820,490 710,505" fill="var(--gold-light)"/>
      <polygon points="650,305 735,310 735,485 650,460" fill="var(--gold-dark)"/>
      <polygon points="735,310 800,305 800,475 735,480" fill="var(--gold-light)"/>
      <polygon points="705,290 820,285 820,305 705,310" fill="var(--gold-top)"/>
      <circle class="icon-fill" cx="766" cy="302" r="11"/>
      <circle cx="768" cy="299" r="3.5" fill="var(--gold-light)"/>
      <text class="pillar-label" transform="translate(778,470) rotate(-90)">Intelligence</text>
    </g>

    <!-- pillar: innovation -->
    <g class="pillar pillar-innovation">
      <polygon points="495,485 680,480 680,510 540,530 495,505" fill="var(--blue-dark)"/>
      <polygon points="540,505 680,480 680,510 540,530" fill="var(--blue-light)"/>
      <polygon points="495,330 575,330 575,500 495,480" fill="var(--blue-dark)"/>
      <polygon points="575,330 640,325 640,495 575,500" fill="var(--blue-light)"/>
      <polygon points="555,305 670,298 670,318 555,333" fill="var(--blue-top)"/>
      <rect class="icon-fill" x="600" y="322" width="9" height="9"/>
      <rect class="icon-fill" x="611" y="315" width="9" height="9"/>
      <text class="pillar-label" transform="translate(620,498) rotate(-90)">Innovation</text>
    </g>

    <!-- pillar: people -->
    <g class="pillar pillar-people">
      <polygon points="245,450 430,530 520,520 520,545 400,555 245,475" fill="var(--green-dark)"/>
      <polygon points="400,535 520,520 520,545 400,555" fill="var(--green-light)"/>
      <polygon points="265,290 430,345 430,532 265,460" fill="var(--green-dark)"/>
      <polygon points="430,345 495,340 495,525 430,532" fill="var(--green-light)"/>
      <polygon points="400,330 515,320 515,346 400,352" fill="var(--green-top)"/>
      <g class="icon-fill">
        <circle cx="452" cy="340" r="3.2"/><rect x="449" y="345" width="6" height="16"/>
        <circle cx="463" cy="340" r="3.2"/><rect x="460" y="345" width="6" height="16"/>
        <circle cx="472" cy="352" r="2.4"/><rect x="470" y="356" width="4.5" height="8"/>
      </g>
      <text class="pillar-label" transform="translate(470,484) rotate(-90)">People</text>
    </g>

    <!-- roof -->
    <g class="roof">
      <polygon points="240,250 365,305 365,335 240,280" fill="var(--beam-end)"/>
      <polygon points="365,305 1005,225 1005,250 365,335" fill="var(--beam)"/>
      <polygon points="270,252 575,22 700,75 390,300" fill="var(--roof-light)"/>
      <polygon points="390,300 700,75 1000,225" fill="var(--roof-frame)"/>
      <polygon points="432,288 552,196 665,256" fill="var(--roof-panel)"/>
      <polygon points="562,185 700,84 810,142 680,240" fill="var(--roof-panel)"/>
      <polygon points="715,247 830,157 945,214" fill="var(--roof-panel)"/>
      <text class="roof-label" transform="translate(516,258) rotate(-8)">Leader</text>
      <text class="roof-label" transform="translate(637,178) rotate(-8)">Partner</text>
      <text class="roof-label" transform="translate(765,225) rotate(-8)">Profitability</text>
    </g>
  </svg>
</main>
</body>
</html>
```